Web Design for a Biotech Consulting Firm

We need a web site design for a new business based in Philadelphia called Verantel Dx. This is a consulting firm that will serve medical diagnostics industry, which is part of the life science/healthcare industry focusing on developing and marketing products that help in early detection, monitoring or management of diseases. Our consulting firm will help medical diagnostic companies to overcome key challenges in designing, evaluating and marketing new products.Our company name is Verantel Dx. Verantel is Latin word for "something" Dx represents diagnostics. The idea behind the name is that we help companies to transform the original, early product ideas ("nothing") into "something"; which is a product with full clinical utility that will help to improve health and well-being.The web site should use the visual feel of the logo (attached), be modern, simple and clean looking and represent creativity, innovation, scientific thinking and progress.
Updates

Wix Design is acceptable

Industry/Entity Type

Biotechnology

Coding

Coded - Design and coding required

Number of Pages Required

1 page

Font styles to use
Sans Serif

Requirements
Must have
• simple, clean look couple of pages
Should not have
• a lot of pages

```html
<!DOCTYPE html>
<html lang="en">
<head>
<meta charset="utf-8">
<title>Verantel Dx — Biotech Consulting</title>
<link rel="stylesheet" href="https://fonts.googleapis.com/css2?family=Montserrat:wght@400;500;600;700;800;900&display=swap">
<style>
:root{
  --blue:#1b7ff0;
  --ink:#1c1c1c;
  --text:#3a3a3a;
  --muted:#6d6d6d;
  --dark:#17181c;
  --black:#000;
  --white:#fff;
  --star:#f47a20;
  --line:#dcdcdc;
}
*{margin:0;padding:0;box-sizing:border-box}
html,body{width:1200px;height:3069px;overflow:hidden}
body{font-family:'Montserrat',sans-serif;background:var(--white);color:var(--text);position:relative}
.abs{position:absolute}

/* header */
.site-header{position:absolute;left:0;top:0;width:1200px;height:113px;border-bottom:2px solid #d6d6d6;background:var(--white)}
.brand{position:absolute;left:158px;top:42px;font-size:22px;font-weight:500;color:var(--ink);white-space:nowrap;line-height:28px}
.header-phone{position:absolute;right:146px;top:22px;display:flex;align-items:center;gap:10px;font-size:16px;color:#444}
.header-phone .icon{width:24px;height:24px;background:var(--blue);border-radius:4px;display:flex;align-items:center;justify-content:center}
.main-nav{position:absolute;right:146px;top:61px;display:flex;font-size:15px;font-weight:500;color:#444}
.main-nav a{text-decoration:none;color:inherit;padding:5px 19px;border:2px solid transparent}
.main-nav a.active{border-color:var(--blue);color:var(--blue)}

/* hero */
.hero{position:absolute;left:0;top:113px;width:1200px;height:614px;overflow:hidden}
.hero-photo{position:absolute;inset:0;background:linear-gradient(115deg,#b84a3a 0%,#c98878 28%,#9aa3b8 55%,#6e7890 80%,#59637c 100%)}
.hero-shade{position:absolute;inset:0;background:radial-gradient(ellipse at 55% 30%,rgba(240,210,190,.35),transparent 60%)}
.hero-title{position:absolute;left:0;width:1200px;top:193px;text-align:center;font-size:38px;font-weight:900;color:var(--white);text-shadow:0 2px 4px rgba(0,0,0,.35);letter-spacing:-.5px}
.hero-sub{position:absolute;left:295px;width:610px;top:251px;text-align:center;font-size:16.5px;line-height:26px;font-weight:500;color:var(--white)}
.btn{display:inline-flex;align-items:center;justify-content:center;background:var(--blue);color:var(--white);font-weight:700;text-decoration:none;text-transform:uppercase}
.hero .btn{position:absolute;left:522px;top:316px;width:158px;height:48px;font-size:16px}
.dots{position:absolute;left:1118px;top:278px;display:flex;flex-direction:column;align-items:center;gap:12px}
.dots i{display:block;width:9px;height:9px;border-radius:50%;background:var(--white)}
.dots i.on{width:18px;height:18px;border:3px solid var(--white);background:transparent;position:relative}
.dots i.on::after{content:"";position:absolute;left:3px;top:3px;width:6px;height:6px;border-radius:50%;background:var(--white)}

/* about */
.about-photo{position:absolute;left:141px;top:800px;width:398px;height:398px}
.about-text{position:absolute;left:595px;top:822px;width:466px}
.about-text .eyebrow{font-size:22px;font-weight:500;color:var(--ink)}
.about-text h2{font-size:38px;font-weight:800;color:var(--black);margin-top:8px}
.about-text p{font-size:15.5px;line-height:28px;text-align:justify;color:#333;margin-top:14px}
.about-text .btn{width:168px;height:53px;font-size:16px;margin-top:24px}

/* services */
.services{position:absolute;left:0;top:1270px;width:1200px;height:870px;overflow:hidden}
.services-bg{position:absolute;left:0;top:0;width:1200px;height:870px}
.section-title{position:absolute;left:0;width:1200px;text-align:center;font-weight:800}
.services .section-title{top:146px;font-size:38px;color:var(--white)}
.service{position:absolute;top:276px;width:314px;text-align:center;color:var(--white)}
.service .frame{position:relative;width:314px;height:280px}
.service h3{font-size:23px;font-weight:600;margin-top:20px}
.service p{font-size:16.5px;line-height:26px;color:#e6e6e6;margin-top:20px;padding:0 10px}

/* testimonials */
.testimonials .section-title{top:2200px;font-size:38px;color:var(--black)}
.quote{position:absolute;top:2330px;width:275px;text-align:center}
.quote .bubble{position:relative;background:var(--white);border-radius:8px;box-shadow:0 2px 12px rgba(0,0,0,.16);padding:52px 18px 18px;font-size:12px;line-height:22.5px;color:#555}
.quote .bubble::after{content:"";position:absolute;left:50%;bottom:-9px;margin-left:-9px;width:18px;height:18px;background:var(--white);transform:rotate(45deg);box-shadow:4px 4px 6px rgba(0,0,0,.08)}
.quote .avatar{position:absolute;left:95px;top:-44px;width:84px;height:84px;border-radius:50%;border:3px solid var(--white);background:linear-gradient(160deg,#d6b6a2,#8b6453);z-index:2;box-shadow:0 1px 4px rgba(0,0,0,.2)}
.quote .who{margin-top:52px;font-size:16px;font-weight:600;color:var(--ink)}
.quote .date{font-size:13px;color:#555;margin-top:6px}
.quote .stars{margin-top:8px;display:flex;gap:5px;justify-content:center}

/* footer */
.site-footer{position:absolute;left:0;top:2660px;width:1200px;height:409px;overflow:hidden;color:var(--white)}
.footer-col{position:absolute;top:150px}
.footer-col h4{font-size:20px;font-weight:600;margin-bottom:16px}
.footer-col ul{list-style:none;font-size:12px;line-height:27px}
.contact-item{display:flex;gap:8px;font-size:13px;line-height:22px;margin-bottom:16px}
.contact-item svg{flex:none;margin-top:3px}
.email-input{width:242px;height:36px;background:var(--white);color:#555;font-size:12px;padding:0 13px;display:flex;align-items:center}
.subscribe{width:125px;height:36px;font-size:15px;margin-top:20px}
.footer-rule{position:absolute;left:110px;top:337px;width:939px;height:1px;background:#333}
.copyright{position:absolute;left:134px;top:362px;font-size:12px}
.social{position:absolute;left:906px;top:362px;display:flex;gap:17px}
.social i{display:block;width:14px;height:14px;border-radius:50%;background:var(--white)}
</style>
</head>
<body>

<header class="site-header">
  <div class="brand">Verantel Dx</div>
  <div class="header-phone">
    <span class="icon"><svg width="14" height="14" viewBox="0 0 24 24"><path fill="#fff" d="M6.6 10.8a15.1 15.1 0 0 0 6.6 6.6l2.2-2.2a1 1 0 0 1 1-.25 11.4 11.4 0 0 0 3.6.57 1 1 0 0 1 1 1V20a1 1 0 0 1-1 1A17 17 0 0 1 3 4a1 1 0 0 1 1-1h3.5a1 1 0 0 1 1 1c0 1.25.2 2.45.57 3.57a1 1 0 0 1-.25 1z"/></svg></span>
    +01 23 555 0142
  </div>
  <nav class="main-nav">
    <a class="active" href="#">Home</a><a href="#">About Us</a><a href="#">Services</a><a href="#">News</a><a href="#" style="padding-right:0">Contact Us</a>
  </nav>
</header>

<section class="hero">
  <div class="hero-photo" role="img" aria-label="Clinician preparing a patient for an MRI scan, warm red to cool blue tint"></div>
  <div class="hero-shade"></div>
  <h1 class="hero-title">WE ARE A BIOTECH CONSULTING FIRM</h1>
  <p class="hero-sub">Lorem ipsum dolor sit amet, consectetur adipiscing elit, sed do eiusmod tempor incididunt ut labore et dolore magna aliqua.</p>
  <a class="btn" href="#">Read More</a>
  <div class="dots"><i class="on"></i><i></i><i></i></div>
  <svg class="abs" style="left:0;top:0" width="1200" height="614" viewBox="0 0 1200 614">
    <path fill="#fff" d="M0 585 C150 535 330 520 560 545 C800 572 1000 614 1200 600 L1200 614 L0 614Z"/>
    <path fill="none" stroke="var(--blue)" stroke-width="6" d="M0 590 C150 545 330 530 560 555 C800 582 1000 622 1200 606"/>
  </svg>
</section>

<section class="about">
  <svg class="about-photo" viewBox="0 0 398 398">
    <circle cx="199" cy="199" r="196" fill="none" stroke="var(--blue)" stroke-width="6"/>
    <circle cx="190" cy="203" r="188" fill="#f3f1ea"/>
  </svg>
  <div class="abs" role="img" aria-label="MRI scanner in a bright hospital room" style="left:148px;top:818px;width:382px;height:382px;border-radius:50%;background:radial-gradient(circle at 45% 45%,#f4f6fb 0%,#dfe3ee 45%,#b9c2d6 75%,#9aa6c0 100%)"></div>
  <div class="about-text">
    <div class="eyebrow">About Us</div>
    <h2>Verantel Dx</h2>
    <p>Lorem ipsum dolor sit amet, consectetur adipiscing elit, sed do eiusmod tempor incididunt ut labore et dolore magna aliqua. Ut enim ad minim veniam, quis nostrud exercitation ullamco laboris nisi ut aliquip ex ea commodo consequat. Duis aute irure dolor in reprehenderit in voluptate velit esse cillum dolore eu fugiat nulla pariatur.</p>
    <a class="btn" href="#">Read More</a>
  </div>
</section>

<section class="services">
  <svg class="services-bg" viewBox="0 0 1200 870">
    <defs>
      <linearGradient id="svcTone" x1="0" y1="0" x2="1" y2="1">
        <stop offset="0" stop-color="#25272d"/><stop offset=".5" stop-color="#16171b"/><stop offset="1" stop-color="#1d1f24"/>
      </linearGradient>
    </defs>
    <path fill="url(#svcTone)" d="M0 44 C120 16 300 12 560 40 C820 68 1050 80 1200 30 L1200 790 C1050 850 850 860 600 830 C350 800 150 770 0 800Z"/>
    <path fill="none" stroke="var(--blue)" stroke-width="5" d="M0 32 C120 4 300 0 560 28 C820 56 1050 66 1200 20"/>
    <path fill="none" stroke="var(--blue)" stroke-width="6" d="M0 818 C150 780 350 800 600 838 C850 866 1050 860 1200 800"/>
  </svg>
  <h2 class="section-title">Our Services</h2>

  <div class="service" style="left:80px">
    <svg class="frame" viewBox="0 0 314 280"><path fill="#fff" d="M30 4 L290 20 Q314 24 313 48 L303 250 Q300 272 276 272 L30 276 Q6 276 4 252 L0 30 Q0 4 30 4Z"/></svg>
    <div class="abs" role="img" aria-label="Blood pressure monitor on a patient's arm" style="left:0;top:12px;width:290px;height:258px;border-radius:18px;background:linear-gradient(135deg,#3a3d46,#b9b4ad 55%,#e7e2d8)"></div>
    <h3>Lorem ipsum dolor</h3>
    <p>Sed ut perspiciatis unde omnis iste natus error sit voluptatem accusantium doloremque</p>
  </div>
  <div class="service" style="left:439px">
    <svg class="frame" viewBox="0 0 314 280"><path fill="#fff" d="M30 4 L290 20 Q314 24 313 48 L303 250 Q300 272 276 272 L30 276 Q6 276 4 252 L0 30 Q0 4 30 4Z"/></svg>
    <div class="abs" role="img" aria-label="Gloved hand placing sample tubes into a centrifuge" style="left:4px;top:12px;width:286px;height:258px;border-radius:18px;background:linear-gradient(150deg,#f1f3f6,#c9d7e6 50%,#2a7fd0 80%,#e4e8ee)"></div>
    <h3>Lorem ipsum dolor</h3>
    <p>Sed ut perspiciatis unde omnis iste natus error sit voluptatem accusantium doloremque</p>
  </div>
  <div class="service" style="left:797px">
    <svg class="frame" viewBox="0 0 314 280"><path fill="#fff" d="M30 4 L290 20 Q314 24 313 48 L303 250 Q300 272 276 272 L30 276 Q6 276 4 252 L0 30 Q0 4 30 4Z"/></svg>
    <div class="abs" role="img" aria-label="Doctor performing an ultrasound scan" style="left:4px;top:12px;width:286px;height:258px;border-radius:18px;background:linear-gradient(120deg,#6c6462,#e9ebee 45%,#b8c1cc 75%,#eef0f2)"></div>
    <h3>Lorem ipsum dolor</h3>
    <p>Sed ut perspiciatis unde omnis iste natus error sit voluptatem accusantium doloremque</p>
  </div>
</section>

<section class="testimonials">
  <h2 class="section-title">Testimonials</h2>

  <div class="quote" style="left:149px">
    <div class="avatar" role="img" aria-label="Client portrait"></div>
    <div class="bubble">Sed ut perspiciatis unde omnis iste natus error sit voluptatem accusantium doloremque laudantium, totam rem aperiam, eaque ipsa quae</div>
    <div class="who">M.P , England</div>
    <div class="date">April 04, 2019</div>
    <div class="stars"><svg width="72" height="12" viewBox="0 0 72 12"><g fill="var(--star)"><path id="st" d="M6 0l1.8 3.9 4.2.4-3.2 2.8 1 4.1L6 9 2.2 11.2l1-4.1L0 4.3l4.2-.4z"/><use href="#st" x="15"/><use href="#st" x="30"/><use href="#st" x="45"/><use href="#st" x="60"/></g></svg></div>
  </div>
  <div class="quote" style="left:461px">
    <div class="avatar" role="img" aria-label="Client portrait"></div>
    <div class="bubble">Sed ut perspiciatis unde omnis iste natus error sit voluptatem accusantium doloremque laudantium, totam rem aperiam, eaque ipsa quae</div>
    <div class="who" style="margin-top:50px">I.M, France</div>
    <div class="date">February 18, 2019</div>
    <div class="stars"><svg width="72" height="12" viewBox="0 0 72 12"><g fill="var(--star)"><use href="#st"/><use href="#st" x="15"/><use href="#st" x="30"/><use href="#st" x="45"/><use href="#st" x="60"/></g></svg></div>
  </div>
  <div class="quote" style="left:773px">
    <div class="avatar" role="img" aria-label="Client portrait" style="background:linear-gradient(160deg,#a9c3d6,#3c5a78)"></div>
    <div class="bubble">Sed ut perspiciatis unde omnis iste natus error sit voluptatem accusantium doloremque laudantium, totam rem aperiam, eaque ipsa quae</div>
    <div class="who" style="margin-top:34px">DJ, UK</div>
    <div class="date">January 20, 2019</div>
    <div class="stars"><svg width="72" height="12" viewBox="0 0 72 12"><g fill="var(--star)"><use href="#st"/><use href="#st" x="15"/><use href="#st" x="30"/><use href="#st" x="45"/><use href="#st" x="60"/></g></svg></div>
  </div>
</section>

<footer class="site-footer">
  <svg class="abs" style="left:0;top:0" width="1200" height="409" viewBox="0 0 1200 409">
    <path fill="var(--black)" d="M0 40 C180 0 380 10 600 60 C820 110 1000 110 1200 40 L1200 409 L0 409Z"/>
    <path fill="none" stroke="var(--blue)" stroke-width="6" d="M500 45 C700 95 900 125 1200 50"/>
  </svg>

  <div class="footer-col" style="left:134px">
    <h4>Contact Us</h4>
    <div class="contact-item"><svg width="16" height="20" viewBox="0 0 16 20"><path fill="none" stroke="#fff" stroke-width="1.3" d="M8 1a6 6 0 0 1 6 6c0 4.5-6 11-6 11S2 11.5 2 7a6 6 0 0 1 6-6z"/><circle cx="8" cy="7" r="2.2" fill="none" stroke="#fff" stroke-width="1.3"/></svg><span>#10, Sed ut perspiciatis unde<br>omnis iste natus error</span></div>
    <div class="contact-item"><svg width="18" height="18" viewBox="0 0 24 24"><path fill="none" stroke="#fff" stroke-width="1.5" d="M6.6 10.8a15.1 15.1 0 0 0 6.6 6.6l2.2-2.2a1 1 0 0 1 1-.25 11.4 11.4 0 0 0 3.6.57 1 1 0 0 1 1 1V20a1 1 0 0 1-1 1A17 17 0 0 1 3 4a1 1 0 0 1 1-1h3.5a1 1 0 0 1 1 1c0 1.25.2 2.45.57 3.57a1 1 0 0 1-.25 1z"/></svg><span>+01 23 555 0142</span></div>
    <div class="contact-item"><svg width="20" height="16" viewBox="0 0 20 16"><rect x="1" y="1" width="18" height="14" fill="none" stroke="#fff" stroke-width="1.3"/><path fill="none" stroke="#fff" stroke-width="1.3" d="M1 1l9 8 9-8M1 15l6-6M19 15l-6-6"/></svg><span>info@verantel-dx.com</span></div>
  </div>
  <div class="footer-col" style="left:416px">
    <h4>Quick Links</h4>
    <ul style="padding-left:4px"><li>Home</li><li>About Us</li><li>Services</li><li>News</li><li>Contact Us</li></ul>
  </div>
  <div class="footer-col" style="left:593px">
    <h4>Other Links</h4>
    <ul style="padding-left:3px"><li>Faq</li><li>Privacy Policy</li><li>Terms &amp; Conditions</li></ul>
  </div>
  <div class="footer-col" style="left:803px">
    <h4>Newsletter</h4>
    <div class="email-input">Email ID</div>
    <a class="btn subscribe" href="#" style="text-transform:none">Subscribe</a>
  </div>

  <div class="footer-rule"></div>
  <div class="copyright">Copyrights © 2019. Allrights Reserved.</div>
  <div class="social" aria-label="Social links"><i></i><i></i><i></i><i></i><i></i></div>
</footer>

</body>
</html>
```